jQuery Mobile CSS for web app

Task Outline:
Create jQuery Mobile themeroller compliant CSS and icons for a mobile web app.
Task Description:
Brindle Solutions are in the process of implementing a new, web based version of their Tessel operations platform.
The web based version of Tessel is built on top of the jQuery Mobile platform and we are looking for a designer to create a jQuery Mobile themeroller compliant CSS theme pack that we can plug into our application. The aim is to remove the standard jQuery Mobile look and feel and to introduce the Brindle branding throughout the new web app.
A number of screenshots are shown in the attached design spec (brindle_solutions.pdf) that show what the current (Windows Mobile 6.5) application looks like, alongside the development version of our new web app.
Deliverables:
• jQuery Mobile (v 1.4.2) themeroller compliant CSS which provides theming for all jQuery Mobile UI components.
• Example html showing how to use the CSS theme (especially where additional html/css classes are required).
• New set of status icons (as listed in attachment)
Inspiration:
See our website for current branding: www.brindle-solutions-demo.net

```html
<!DOCTYPE html>
<html lang="en">
<head>
<meta charset="utf-8">
<title>Brindle Tessel – Launchpad</title>
<link rel="stylesheet" href="https://fonts.googleapis.com/css2?family=Open+Sans:wght@300;400;600&family=Roboto:wght@400&display=swap">
<style>
  :root {
    --brand-red: #c8101a;
    --header-black: #000000;
    --menu-grey: #7a7a7a;
    --band-grey: #ebebeb;
    --page-bg: #f4f4f4;
    --card-bg: #fafafa;
    --white: #ffffff;
    --border: #e3e3e3;
    --text: #4a4a4a;
    --text-dark: #333333;
    --icon-grey: #d3d3d3;
    --icon-slate: #5a6a7e;
  }
  * { box-sizing: border-box; margin: 0; padding: 0; }
  html, body { width: 795px; height: 1200px; overflow: hidden; }
  body {
    position: relative;
    background: var(--page-bg);
    font-family: "Open Sans", Arial, sans-serif;
    color: var(--text);
  }
  .app-header {
    position: absolute; left: 0; top: 0; width: 795px; height: 158px;
    background: var(--header-black);
  }
  .app-title {
    position: absolute; left: 202px; top: 56px;
    font-family: "Roboto", Arial, sans-serif;
    font-size: 41px; line-height: 50px; color: var(--white);
    letter-spacing: -0.3px;
  }
  .menu-button {
    position: absolute; left: 666px; top: 46px; width: 72px; height: 69px;
    background: var(--menu-grey); border-radius: 5px;
    display: flex; align-items: center; justify-content: center;
  }
  .page-band {
    position: absolute; left: 0; top: 158px; width: 795px; height: 136px;
    background: var(--band-grey);
  }
  .page-title {
    position: absolute; left: 42px; top: 44px;
    font-size: 41px; line-height: 52px; color: var(--brand-red);
  }
  .section-label {
    position: absolute; left: 43px;
    font-size: 28px; line-height: 36px; color: var(--text);
  }
  .filter-button {
    position: absolute; top: 415px; height: 95px;
    display: flex; align-items: center; justify-content: center;
    font-size: 24px; color: var(--text);
    background: var(--white); border: 1px solid #ececec;
  }
  .filter-button.is-active { background: var(--brand-red); color: var(--white); border-color: var(--brand-red); }
  .search-button {
    position: absolute; left: 46px; top: 545px; width: 217px; height: 73px;
    background: var(--brand-red); color: var(--white);
    display: flex; align-items: center; gap: 32px; padding-left: 24px;
    font-size: 30px;
  }
  .result-card {
    position: absolute; left: 45px; width: 705px; height: 108px;
    background: var(--card-bg); border: 1px solid var(--border);
  }
  .result-icon { position: absolute; left: 22px; top: 20px; }
  .result-id, .result-desc {
    position: absolute; left: 113px; font-size: 24px; line-height: 30px; color: var(--text-dark);
  }
  .result-id { top: 14px; }
  .result-desc { top: 58px; }
  .app-footer {
    position: absolute; left: 0; top: 1028px; width: 795px; height: 172px;
    display: flex; background: var(--page-bg);
  }
  .footer-tab {
    flex: 1; position: relative; background: #f8f8f8;
    border-top: 1px solid var(--border); border-right: 1px solid var(--border);
    display: flex; flex-direction: column; align-items: center;
  }
  .footer-tab:last-child { border-right: none; }
  .footer-tab svg { margin-top: 30px; }
  .footer-label { margin-top: 14px; font-size: 31px; font-weight: 300; color: var(--text); }
  .screen-code {
    position: absolute; left: 746px; top: 1150px;
    font-family: Arial, sans-serif; font-size: 20px; color: #000;
  }
</style>
</head>
<body>
  <header class="app-header">
    <div class="app-title">Brindle Tessel</div>
    <div class="menu-button">
      <svg width="26" height="20" viewBox="0 0 26 20"><rect y="2" width="26" height="3" fill="#2e3a48"/><rect y="8.5" width="26" height="3" fill="#2e3a48"/><rect y="15" width="26" height="3" fill="#2e3a48"/></svg>
    </div>
  </header>

  <div class="page-band"><h1 class="page-title">Launchpad</h1></div>

  <div class="section-label" style="top:346px">Cable</div>

  <div class="filter-button" style="left:45px;width:189px">Serial No</div>
  <div class="filter-button" style="left:266px;width:189px">Item No</div>
  <div class="filter-button is-active" style="left:488px;width:261px">Description</div>

  <div class="search-button">Search
    <svg width="32" height="32" viewBox="0 0 32 32"><circle cx="12" cy="12" r="8" fill="none" stroke="#fff" stroke-width="3.5"/><line x1="18" y1="18" x2="28" y2="28" stroke="#fff" stroke-width="5" stroke-linecap="round"/></svg>
  </div>

  <div class="section-label" style="top:660px">Result</div>

  <div class="result-card" style="top:737px">
    <svg class="result-icon" width="68" height="68" viewBox="0 0 68 68"><circle cx="34" cy="34" r="34" fill="var(--icon-grey)"/><path d="M34 34 L34 0 M34 34 L68 34 M34 34 L10 58" stroke="#fafafa" stroke-width="3"/></svg>
    <div class="result-id">30106</div>
    <div class="result-desc">RAD64002143 ; L 62 ca..</div>
  </div>
  <div class="result-card" style="top:866px">
    <svg class="result-icon" width="68" height="68" viewBox="0 0 68 68"><circle cx="34" cy="34" r="34" fill="var(--icon-grey)"/><path d="M34 34 L34 0 M34 34 L68 34 M34 34 L10 58" stroke="#fafafa" stroke-width="3"/></svg>
    <div class="result-id">30106</div>
    <div class="result-desc">RAD64002143 ; L 62 ca..</div>
  </div>

  <nav class="app-footer">
    <div class="footer-tab">
      <svg width="58" height="58" viewBox="0 0 58 58"><circle cx="29" cy="29" r="26" fill="none" stroke="var(--brand-red)" stroke-width="4"/><path d="M16 29 L26 21 L26 26 L41 26 L41 32 L26 32 L26 37 Z" fill="var(--brand-red)"/></svg>
      <span class="footer-label">BACK</span>
    </div>
    <div class="footer-tab">
      <svg width="58" height="58" viewBox="0 0 58 58"><g fill="var(--icon-slate)"><rect x="7" y="12" width="7" height="6"/><rect x="17" y="12" width="34" height="6"/><rect x="7" y="26" width="7" height="6"/><rect x="17" y="26" width="34" height="6"/><rect x="7" y="40" width="7" height="6"/><rect x="17" y="40" width="34" height="6"/></g></svg>
      <span class="footer-label">TASKS</span>
    </div>
    <div class="footer-tab">
      <svg width="58" height="58" viewBox="0 0 58 58"><circle cx="29" cy="29" r="26" fill="none" stroke="var(--brand-red)" stroke-width="4"/><path d="M42 29 L32 21 L32 26 L17 26 L17 32 L32 32 L32 37 Z" fill="var(--brand-red)"/></svg>
      <span class="footer-label">NEXT</span>
    </div>
  </nav>
  <div class="screen-code">C7</div>
</body>
</html>
```